Need Business Card ASAP

We need a business card design for a meeting coming up in a few days. The company name is Harlow Ridge Building and Construction and the logo is attached. Something clean, cool, and contemporary that we can get to a printer right away. Attached is the business card for Volmar Energy, an affiliated company, which we like. Instead of the hawk on the back, you could use the attached "D". We'll also be needing matching letterhead in the near future, so ideas for that are welcome.

```html
<!DOCTYPE html>
<html lang="en">
<head>
<meta charset="utf-8">
<title>Harlow Ridge Building and Construction — Business Card</title>
<link href="https://fonts.googleapis.com/css2?family=Source+Sans+3:wght@400;600;700&display=swap" rel="stylesheet">
<style>
  :root {
    --backdrop: #e6e2da;
    --paper: #ffffff;
    --khaki: #c9c597;
    --khaki-light: #e2dfc6;
    --ink: #231f20;
    --grey-text: #555555;
    --sans: "Source Sans 3", "Helvetica Neue", Arial, sans-serif;
  }
  * { margin: 0; padding: 0; box-sizing: border-box; }
  html, body {
    width: 1034px; height: 1200px; overflow: hidden;
    background: var(--backdrop);
    font-family: var(--sans);
    color: var(--ink);
  }
  .canvas { position: relative; width: 1034px; height: 1200px; }

  .card { position: absolute; left: 73px; width: 885px; height: 504px; }
  .card--front { top: 59px; background: var(--paper); }
  .card--back { top: 602px; background: var(--khaki); }

  /* front: brand tile */
  .brand-tile {
    position: absolute; left: 57px; top: 85px; width: 264px; height: 338px;
    display: flex; flex-direction: column; justify-content: center; align-items: flex-start;
    padding: 0 26px; gap: 22px;
  }
  .brand-tile__square { width: 70px; height: 70px; background: var(--khaki); }
  .brand-tile__name {
    font-size: 30px; font-weight: 600; line-height: 1.15; color: var(--ink);
  }

  /* front: vertical web bar */
  .web-bar {
    position: absolute; left: 405px; top: 76px; width: 46px; height: 355px;
    background: var(--ink);
    display: flex; align-items: center; justify-content: center;
  }
  .web-bar__text {
    transform: rotate(-90deg); white-space: nowrap;
    color: #fff; font-size: 21px; letter-spacing: 1.5px;
  }

  /* front: contact panel */
  .contact-panel {
    position: absolute; left: 463px; top: 76px; right: 0; height: 355px;
    background: linear-gradient(180deg, var(--khaki) 0%, var(--khaki-light) 100%);
    padding: 14px 0 0 24px;
  }
  .contact-panel__name { font-size: 30px; font-weight: 700; line-height: 1.1; }
  .contact-panel__title { font-size: 18px; font-weight: 700; margin-top: 4px; }
  .contact-list { list-style: none; margin-top: 10px; }
  .contact-list li {
    display: flex; align-items: center; gap: 9px;
    font-size: 24px; height: 48px;
  }
  .contact-list svg { width: 18px; height: 20px; fill: var(--ink); flex: none; }
  .contact-panel__company { font-size: 24px; line-height: 30px; margin-top: 6px; }
  .contact-panel__address { font-size: 20px; margin-top: 16px; }

  /* back */
  .back-mark {
    position: absolute; left: 40px; top: 118px; width: 420px;
    display: flex; flex-direction: column; gap: 20px;
  }
  .back-mark__square { width: 110px; height: 110px; background: var(--paper); }
  .back-mark__name { font-size: 56px; font-weight: 600; line-height: 1.05; color: var(--paper); }
  .back-web {
    position: absolute; left: 458px; top: 234px;
    font-size: 25px; font-weight: 700; color: var(--grey-text);
  }
</style>
</head>
<body>
<main class="canvas">

  <section class="card card--front" aria-label="Business card front">
    <div class="brand-tile">
      <div class="brand-tile__square"></div>
      <div class="brand-tile__name">Harlow Ridge<br>Building and<br>Construction</div>
    </div>

    <div class="web-bar"><span class="web-bar__text">www.harlowridge.com</span></div>

    <div class="contact-panel">
      <h1 class="contact-panel__name">Your Name</h1>
      <p class="contact-panel__title">Title</p>
      <ul class="contact-list">
        <li>
          <svg viewBox="0 0 20 20" aria-hidden="true"><path d="M5 2l3 4-2 2c1 2.5 3.5 5 6 6l2-2 4 3-2 3C9 18 2 11 2 4z"/></svg>
          (123) 456-7890
        </li>
        <li>
          <svg viewBox="0 0 20 20" aria-hidden="true"><path d="M6 1h8a1 1 0 011 1v16a1 1 0 01-1 1H6a1 1 0 01-1-1V2a1 1 0 011-1zm1 3v9h6V4zm3 11.5a1 1 0 100 2 1 1 0 000-2z"/></svg>
          (123) 456-7890
        </li>
        <li>
          <svg viewBox="0 0 20 20" aria-hidden="true"><path d="M2 8l8-5 8 5v9H2zm2 1.2V15h12V9.2l-6 3.8z"/></svg>
          yourname@harlowridge.com
        </li>
      </ul>
      <p class="contact-panel__company">Harlow Ridge Building<br>&amp; Construction</p>
      <p class="contact-panel__address">00, Complex Name, Street, City 00000</p>
    </div>
  </section>

  <section class="card card--back" aria-label="Business card back">
    <div class="back-mark">
      <div class="back-mark__square"></div>
      <div class="back-mark__name">Harlow Ridge</div>
    </div>
    <p class="back-web">www.harlowridgebuilding.com</p>
  </section>

</main>
</body>
</html>
```